Website Design Project for Beauty & Wellness Professionals

As background information, I have a website that is focused on Beauty & Wellness Professionals:
- Job Search (www.lumarinovo.com)
- Business Classifieds (negocios.lumarinovo.com)
- Freelancer Classifieds (freelancer.lumarinovo.com)
- Course Reviews (cursos.lumarinovo.com)

All those websites use standard templates.

I need a DESIGN for the HOME PAGE (no coding) of the Website Platform that consolidates the four platforms under the same design.

Website designs that we like:
- quelvox.com
- brintmoor.com

Target Market(s)

Brazilian Professionals from Beauty & Wellness sector

Industry/Entity Type

Business

Requirements
Must have
• Website designs that we like:
- quelvox.com
- brintmoor.com

```html
<!DOCTYPE html>
<html lang="en">
<head>
<meta charset="utf-8">
<title>Lumarinovo Beauty – Home</title>
<link rel="stylesheet" href="https://fonts.googleapis.com/css2?family=Arimo:wght@400;700&family=Archivo+Black&family=Ubuntu:wght@500&display=swap">
<style>
:root{
  --nav:#d8764a;
  --nav-line:#e9a17f;
  --teal:#4aa7b8;
  --btn:#5ba4c0;
  --ink:#222;
  --text:#555;
  --muted:#8a8a8a;
  --panel:#ebe3d9;
  --band:rgba(128,196,128,.72);
  --band-line:#5aaa5a;
  --footer:#2b2b2b;
  --footer-text:#c9c9c9;
  --card-head:rgba(80,80,80,.85);
  --accent:#d8764a;
}
*{margin:0;padding:0;box-sizing:border-box}
html,body{width:765px;height:1200px;overflow:hidden;background:#fff}
body{position:relative;font-family:Arimo,Arial,sans-serif;color:var(--text)}
.abs{position:absolute}
.ph{position:absolute;display:block}

.brand{left:90px;top:8px;display:flex;align-items:center;gap:8px}
.brand-dot{width:40px;height:40px;border-radius:50%;background:var(--teal);opacity:.85}
.brand-name{font-size:20px;color:var(--teal);font-weight:400}

.main-nav{left:317px;top:0;width:360px;height:38px;background:var(--nav);border-radius:0 0 5px 5px;display:flex}
.main-nav a{color:#fff;text-decoration:none;font-size:11.5px;display:flex;align-items:center;justify-content:center;border-left:1px solid var(--nav-line)}
.main-nav a:first-child{border-left:0}

.hero{left:88px;top:55px;width:589px;height:255px;background:linear-gradient(90deg,#fff 0%,#f1e4dc 25%,#c9a089 45%,#e8d3c6 65%,#f7f3f1 100%)}
.appt-label{left:89px;top:243px;font-size:13px;color:var(--ink)}
.appt{left:88px;top:262px;width:589px;height:48px;background:var(--band);border:2px solid var(--band-line)}
.field{position:absolute;top:12px;height:21px;background:#fff;font-size:9px;color:#444;padding:6px 6px 0}
.submit{position:absolute;left:543px;top:11px;width:37px;height:23px;background:#222;color:#fff;font-size:10px;display:flex;align-items:center;justify-content:center;border:1px solid #eee}

.offers{left:88px;top:310px;width:589px;height:145px;background:var(--panel)}
.offer{position:absolute;top:18px;width:180px}
.offer .thumb{left:0;top:0;width:64px;height:64px;border-radius:50%;border:3px solid #fff}
.offer h3{position:absolute;left:76px;top:0;font-family:Ubuntu,sans-serif;font-weight:500;font-size:19px;line-height:19px;color:var(--ink)}
.offer p{position:absolute;left:76px;top:45px;width:96px;font-size:9px;line-height:12px;color:var(--muted)}
.offer .read{position:absolute;left:76px;top:96px;width:54px;height:15px;background:#fff;font-size:6px;color:#666;display:flex;align-items:center;justify-content:center;border-radius:2px}

.h-big{font-family:"Archivo Black",sans-serif;color:var(--ink);letter-spacing:.5px}
.welcome-h{left:90px;top:485px;font-size:21px}
.welcome-frame{left:88px;top:520px;width:189px;height:82px;border:1px solid #ddd}
.welcome-p{left:88px;top:611px;width:190px;font-size:8.5px;line-height:10.5px;color:var(--text)}
.welcome-p a{color:var(--accent)}
.section-h{font-size:14px}
.caption{font-size:10px;color:#444;text-align:center;width:74px}
.pop-list{list-style:none;font-size:11px;color:var(--ink)}
.pop-list li{height:21px;display:flex;align-items:center;gap:8px}
.pop-list .tri{width:0;height:0;border-left:4px solid #222;border-top:3px solid transparent;border-bottom:3px solid transparent}

.rule{left:88px;top:658px;width:589px;height:1px;background:#e2e2e2}
.col-h{top:670px;font-size:15px}
.col-text{top:821px;width:175px;font-size:8.5px;line-height:12.6px;color:var(--text)}
.bullets{list-style:none;top:817px;font-size:8.5px;color:var(--text)}
.bullets li{height:21px;display:flex;align-items:center;gap:8px}
.bullets .tri{width:0;height:0;border-left:4px solid #333;border-top:3px solid transparent;border-bottom:3px solid transparent}
.more{top:912px;width:46px;height:25px;background:var(--btn);color:#fff;font-size:10px;display:flex;align-items:center;justify-content:center;border-radius:2px}

.links-h{left:88px;top:957px;font-size:15px;color:var(--ink);letter-spacing:.3px}
.card{top:989px;width:136px;height:108px;border-radius:8px;overflow:hidden}
.card-head{position:absolute;left:0;top:0;width:100%;height:38px;background:var(--card-head);color:#fff;font-weight:700;font-size:12px;line-height:15px;letter-spacing:.5px;text-align:center;padding-top:6px}
.click{top:1104px;width:136px;text-align:center;font-size:10px;color:#444;text-decoration:underline}

.footer{left:0;top:1133px;width:765px;height:67px;background:var(--footer)}
.foot-nav{position:absolute;left:88px;top:20px;font-size:8.5px;color:var(--footer-text);display:flex;gap:14px}
.copy{position:absolute;left:88px;top:41px;font-size:7.5px;color:#8a8a8a}
.social{position:absolute;left:576px;top:16px;display:flex;gap:5px}
.social span{width:18px;height:18px;border-radius:50%;background:#8a8a8a}
</style>
</head>
<body>

<div class="abs brand"><span class="brand-dot"></span><span class="brand-name">Lumarinovo Beauty</span></div>

<nav class="abs main-nav">
  <a style="width:62px">HOME</a><a style="width:72px">ABOUT US</a><a style="width:74px">SERVICES</a><a style="width:72px">GALLERY</a><a style="width:80px">CONTACT US</a>
</nav>

<div class="ph hero" role="img" aria-label="Woman with long brown hair resting her head on her arm, white background"></div>
<div class="abs appt-label">APPOINTMENT</div>
<form class="abs appt">
  <div class="field" style="left:7px;width:130px">Stylist:</div>
  <div class="field" style="left:141px;width:129px">Date:</div>
  <div class="field" style="left:275px;width:129px">Time:</div>
  <div class="field" style="left:409px;width:129px">Salon:</div>
  <div class="submit">Submit</div>
</form>

<section class="abs offers">
  <div class="offer" style="left:17px">
    <div class="ph thumb" role="img" aria-label="Bride relaxing with a flower in her hair" style="background:radial-gradient(#f0d8cc,#a9785f)"></div>
    <h3>Bridal<br>services</h3>
    <p>Lorem ipsum dolor sit amet consectetuer adipi scing elraesent</p>
    <div class="read">Read More</div>
  </div>
  <div class="offer" style="left:205px">
    <div class="ph thumb" role="img" aria-label="Spa candles and oils" style="background:radial-gradient(#f1d27a,#6f5a2c)"></div>
    <h3>Spa<br>services</h3>
    <p>Consectetuer adipicing elraesent ves tiacean nonuhendrent</p>
    <div class="read">Read More</div>
  </div>
  <div class="offer" style="left:393px">
    <div class="ph thumb" role="img" aria-label="Facial skin care treatment" style="background:radial-gradient(#f4e3d6,#b98d6e)"></div>
    <h3>Facial &amp;<br>skin care</h3>
    <p>Aenean nonum endrerit mauris. Phase llusrce suscipit vius mi</p>
    <div class="read">Read More</div>
  </div>
</section>

<h2 class="abs h-big welcome-h">WELCOME</h2>
<div class="abs welcome-frame"><div class="ph" role="img" aria-label="Close-up of eyes with pink makeup" style="left:6px;top:6px;width:175px;height:69px;background:linear-gradient(90deg,#c9937a,#e7c4b2 50%,#d7aa95)"></div></div>
<p class="abs welcome-p">Nulla ut tempus quam. Aenean augue eros, placerat quis interdum eu, varius vel urna. Fusce vitae posuere nulla, a pellentesque mi. <a>Learn more</a></p>

<h2 class="abs h-big section-h" style="left:316px;top:487px">VIDEO GALLERY</h2>
<div class="ph" role="img" aria-label="Woman with a facial mask" style="left:316px;top:520px;width:74px;height:88px;background:linear-gradient(#c9a486,#e9e2da)"></div>
<div class="ph" role="img" aria-label="Woman receiving a massage" style="left:400px;top:520px;width:73px;height:88px;background:linear-gradient(#d8b39b,#b06a55)"></div>
<div class="abs caption" style="left:316px;top:620px">SPACIAL CARE</div>
<div class="abs caption" style="left:400px;top:618px">MASSAGE</div>

<h2 class="abs h-big section-h" style="left:493px;top:487px;line-height:17px">MOST POPULAR<br>SERVICES</h2>
<ul class="abs pop-list" style="left:497px;top:529px">
  <li><span class="tri"></span>MANICURE</li><li><span class="tri"></span>MAKE-UP</li><li><span class="tri"></span>PEDICURE</li>
</ul>
<ul class="abs pop-list" style="left:596px;top:530px">
  <li>SKIN CARE</li><li>HAIR DESIGN</li><li>PARAFFIN WAX</li>
</ul>

<div class="abs rule"></div>

<h2 class="abs h-big col-h" style="left:88px">WHY CHOOSE US</h2>
<div class="ph" role="img" aria-label="Woman in a towel enjoying a shoulder massage" style="left:88px;top:701px;width:175px;height:106px;background:linear-gradient(90deg,#e9ddd2,#c7977e,#efe6de)"></div>
<p class="abs col-text" style="left:88px;text-align:justify">Ut tristique tellus eu faucibus aliquet. Duis venenatis ultrices lorem ac elementum. Ut laoreet leo sed dapibus mattis. Nulla ac egestas ante. Cras sit amet purus adipiscing, egestas ligula nec, suscipit arcu. Suspendisse sed rutrum risus.</p>
<div class="abs more" style="left:88px">More</div>

<h2 class="abs h-big col-h" style="left:296px">SERVICES</h2>
<div class="ph" role="img" aria-label="Woman with smooth skin posing" style="left:296px;top:701px;width:175px;height:106px;background:linear-gradient(90deg,#fbe0cc,#c48e70,#fbe0cc)"></div>
<ul class="abs bullets" style="left:297px">
  <li><span class="tri"></span>Sui blanditiistes es praetiuptatum</li>
  <li><span class="tri"></span>Welenitimos atququdolores etres</li>
  <li><span class="tri"></span>Euamolestiasexceuri sint timilique</li>
  <li><span class="tri"></span>Suincupaqui officia deserunt</li>
</ul>
<div class="abs more" style="left:296px">More</div>

<h2 class="abs h-big col-h" style="left:501px">OUR MISSION</h2>
<div class="ph" role="img" aria-label="Collage of spa treatments, stones and green oils" style="left:501px;top:708px;width:176px;height:99px;background:linear-gradient(90deg,#b58a72,#6b5a3c 30%,#d9c2b2 50%,#9aa13a 75%,#6b4a33)"></div>
<p class="abs" style="left:501px;top:821px;width:176px;font-size:8.5px;line-height:12.6px"><strong style="color:var(--ink);font-weight:400">Sui blanditiistes es praetiuptatum</strong><br>Eenitimos atququdolores etres quamolestiasex ceuri sint piditaprdentimilique suincupaqui officia deserunt.</p>
<div class="abs more" style="left:501px">More</div>

<h2 class="abs links-h" style="font-weight:400">OUR LINKS:</h2>
<div class="abs card" style="left:88px"><div class="ph" role="img" aria-label="Smiling woman with flowers" style="inset:0;background:linear-gradient(#d9b8a8,#c08670 60%,#e7d6e8)"></div><div class="card-head">JOB<br>SEARCH</div></div>
<div class="abs card" style="left:240px"><div class="ph" role="img" aria-label="Woman relaxing at a spa with a lotus" style="inset:0;background:linear-gradient(#c9a38c,#a8735c 60%,#e6e0c8)"></div><div class="card-head">BUSINESS<br>CLASSIFIEDS</div></div>
<div class="abs card" style="left:390px"><div class="ph" role="img" aria-label="Makeup brushes and powder" style="inset:0;background:linear-gradient(#eadfd6,#c79a7d 60%,#5d5a6e)"></div><div class="card-head">FREELANCER<br>CLASSIFIEDS</div></div>
<div class="abs card" style="left:541px"><div class="ph" role="img" aria-label="Close-up of an eye" style="inset:0;background:linear-gradient(#e8d0c2,#b48772 60%,#d9b9a6)"></div><div class="card-head">COURSE<br>REVIEWS</div></div>
<div class="abs click" style="left:88px">CLICK HERE</div>
<div class="abs click" style="left:240px">CLICK HERE</div>
<div class="abs click" style="left:390px">CLICK HERE</div>
<div class="abs click" style="left:541px">CLICK HERE</div>

<footer class="abs footer">
  <nav class="foot-nav"><span>Home</span><span>|</span><span>About us</span><span>|</span><span>Services</span><span>|</span><span>Gallery</span><span>|</span><span>&nbsp;&nbsp;Blog</span><span>&nbsp;&nbsp;|</span><span>Contact us</span></nav>
  <div class="copy">Copyright 2013 www.lumarinovo.com All Rights Reserved</div>
  <div class="social"><span></span><span></span><span></span><span></span></div>
</footer>

</body>
</html>
```